Stationary Design For Youthful Disability Company

Hi Designers,
Looking to have our brand applied to a range of stationary items to professionalise our approach, we are a disability services company that aligns young carers with disabled youth and adults. Our stationary needs to look professional but can verge into a fun bright territory too.
Winning designer will be first contact for advertising campaign, form creation and web-design in January 2014.
Cheers,
Tom
Brightpath Disability Services
Design Briefs
Stationary.
Sleek fun and bright stationary that portrays a professional but youthful disability service. Company prides its self on delivering youthful carers to disabled clients.
Needed:
- Business Card - Letter Head - Email Signature
- Invoice / Quotation (blank branded paper) - Normal Envelope - A4 Envelope
- Stationary for future forms or documents. (Doesn't need to include all contacts, branding is enough).
Would be nice if we were able to edit numbers etc as we change them.
Include:
Marcus Ferrow - Managing Director
M. 0472 915 408
E. mferrow@brightpathcare.example
A. PO Box 71 Kelsdale 3152
ABN. 58392046115

```html
<!DOCTYPE html>
<html lang="en">
<head>
<meta charset="utf-8">
<title>Brightpath Disability Services – Stationery</title>
<link href="https://fonts.googleapis.com/css2?family=Open+Sans:wght@400;600;700&display=swap" rel="stylesheet">
<style>
  :root{
    --bg:#dcdcdc;
    --paper-edge:#ececec;
    --ink:#8a8a8a;
    --line:#9a9a9a;
    --brand:#1a8ac8;
    --lime:#c8d92a;
    --purple:#7d5ba6;
    --blue:#1a8ac8;
    --orange:#f39020;
    --red:#c0234a;
  }
  *{box-sizing:border-box;margin:0;padding:0}
  html,body{width:1200px;height:1000px;overflow:hidden;background:var(--bg)}
  body{position:relative;font-family:"Open Sans",Arial,sans-serif;color:var(--ink)}
  .sheet{position:absolute;background:linear-gradient(180deg,#fbfbfb 0%,var(--paper-edge) 100%);
    box-shadow:0 1px 4px rgba(0,0,0,.25)}
  .wordmark{font-family:"Open Sans",Arial,sans-serif;font-weight:700;color:var(--brand);
    display:flex;align-items:center;gap:4px;white-space:nowrap;line-height:1}
  .wordmark .dot{width:9px;height:9px;border-radius:50%;background:var(--brand)}
  .sender{position:absolute;font-size:7px;line-height:9px;font-weight:600;color:var(--ink);white-space:nowrap}
  /* letterhead */
  .letterhead{left:47px;top:141px;width:356px;height:504px}
  .letterhead .wordmark{position:absolute;right:46px;top:46px;font-size:10px}
  .letter-body{position:absolute;left:43px;top:120px;width:268px;font-size:6.6px;line-height:12.4px;font-weight:600;color:#8d8d8d;text-align:justify}
  .letter-body p{margin-bottom:12px}
  .letter-body .gap{margin-bottom:0}
  .signature{position:absolute;left:48px;top:338px;width:72px;height:40px;background:linear-gradient(90deg,rgba(120,120,120,.06),rgba(120,120,120,.16),rgba(120,120,120,.04));border-radius:20px}
  /* invoice */
  .invoice{left:424px;top:141px;width:356px;height:504px}
  .invoice .wordmark{position:absolute;right:44px;top:46px;font-size:10px}
  .field{position:absolute;font-size:7px;font-weight:600;color:#8d8d8d;display:flex;align-items:flex-end;gap:3px}
  .field i{display:block;border-bottom:1px solid var(--line);height:7px}
  .item-table{position:absolute;left:49px;top:122px;width:262px;height:290px;border:1px solid var(--line)}
  .item-table .head{height:17px;border-bottom:1px solid var(--line);display:flex;justify-content:space-between;padding:0 20px 0 14px;font-size:8.5px;line-height:17px;color:#8d8d8d;letter-spacing:.3px}
  .item-table .total{position:absolute;left:0;right:0;bottom:0;height:16px;border-top:1px solid var(--line);padding-left:14px;font-size:8.5px;line-height:16px;color:#8d8d8d;letter-spacing:.3px}
  /* A4 envelope */
  .a4-envelope{left:802px;top:141px;width:356px;height:504px;overflow:hidden}
  .a4-flap{position:absolute;left:802px;top:88px}
  .pattern-area{position:absolute;left:164px;top:8px;width:192px;height:492px;border-radius:40px 0 0 40px;
    background:linear-gradient(180deg,#d6e07a 0%,#a98fc6 28%,#6fb3dd 50%,#f6b970 74%,#d9708b 100%);opacity:.85}
  /* DL envelope back */
  .dl-back{left:47px;top:673px;width:356px;height:165px;overflow:hidden}
  .dl-back .ghost-name{position:absolute;left:0;right:0;top:74px;text-align:center;font-size:34px;font-weight:700;color:#d9d9d9}
  .dl-back svg{position:absolute;left:0;top:0}
  /* DL envelope front */
  .dl-front{left:424px;top:673px;width:356px;height:165px}
  .dl-front .wordmark{position:absolute;left:0;right:0;top:70px;justify-content:center;font-size:20px;gap:7px}
  .dl-front .wordmark .dot{width:16px;height:16px}
  /* business cards */
  .card-front{left:802px;top:671px;width:153px;height:85px}
  .card-front .wordmark{position:absolute;left:0;right:0;top:37px;justify-content:center;font-size:10.5px}
  .card-back{left:1006px;top:671px;width:152px;height:85px;overflow:hidden}
  .card-back .mark{position:absolute;left:30px;top:35px;width:14px;height:14px;border-radius:50%;background:#d3d3d3}
  .card-back .details{position:absolute;left:70px;top:23px;font-size:5.6px;line-height:7px;font-weight:600;color:#b4b4b4;white-space:nowrap}
  .card-back .details .name{font-size:7.4px;margin-bottom:3px}
  /* email signature */
  .email{left:802px;top:768px;width:356px;height:192px;background:#fff}
  .toolbar{height:14px;background:linear-gradient(#f4f6f9,#e3e7ee);border-bottom:1px solid #c8ced8;display:flex;align-items:center;gap:3px;padding-left:4px;font-size:5px;color:#333}
  .toolbar b{display:block;width:8px;height:8px;background:#9fb3cc;border-radius:1px}
  .toolbar .sel{width:36px;height:8px;background:#fff;border:1px solid #aab}
  .headers{height:47px;background:#f0f3f7;border-bottom:1px solid #c8ced8;position:relative;font-size:5px;color:#333}
  .hrow{position:absolute;left:8px;display:flex;align-items:center;gap:4px}
  .hrow .box{height:8px;background:#fff;border:1px solid #b9c0cb}
  .suggest{position:absolute;left:44px;top:25px;width:92px;height:20px;background:#fff;border:1px solid #999;font-size:4.5px;line-height:8px;padding-left:2px;color:#2255aa;white-space:nowrap;overflow:hidden}
  .suggest .hi{background:#ffe9a8;color:#333}
  .formatbar{height:10px;background:#eef1f5;border-bottom:1px solid #c8ced8;display:flex;align-items:center;gap:3px;padding-left:5px}
  .formatbar b{display:block;width:7px;height:6px;background:#a8b4c4}
  .formatbar .sel{width:66px;height:7px;background:#fff;border:1px solid #aab}
  .mail-body{padding:6px 6px 0;font-family:Arial,Helvetica,sans-serif;font-size:7px;line-height:9px;color:#222}
  .mail-body p{margin-bottom:7px}
  .mail-body .sign{margin-top:20px}
  .mail-body .addr{font-family:"Open Sans",Arial,sans-serif;font-size:6px;line-height:8px;color:#666;margin-bottom:3px}
  .mail-body .wordmark{font-size:9.5px}
</style>
</head>
<body>

  <!-- Letterhead -->
  <section class="sheet letterhead">
    <div class="sender" style="left:46px;top:43px">Brightpath<br>PO Box 71<br>Kelsdale 3152</div>
    <div class="wordmark"><span class="dot"></span>BRIGHTPATH</div>
    <div class="letter-body">
      <p style="margin-bottom:14px">Dear Mrs Harlow</p>
      <p class="gap">Lorem ipsum dolor sit amet, consectetur adipisicing elit, sed do eiusmod tempor incididunt ut labore et dolore magna aliqua. Ut enim ad minim veniam, quis nostrud exercitation ullamco laboris nisi ut aliquip ex ea commodo consequat. Duis aute irure dolor in reprehenderit in voluptate velit esse cillum dolore eu fugiat nulla pariatur. Excepteur sint occaecat cupidatat non proident, sunt in culpa qui officia deserunt mollit anim id est laborum.</p>
      <p>Lorem ipsum dolor sit amet, consectetur adipisicing elit, sed do eiusmod tempor incididunt ut labore et dolore magna aliqua. Ut enim ad minim veniam, quis nostrud exercitation ullamco laboris nisi ut aliquip ex ea commodo consequat.</p>
      <p>Lorem ipsum dolor sit amet, consectetur adipisicing elit, sed do eiusmod tempor incididunt ut labore et dolore magna aliqua. Ut enim ad minim veniam, quis nostrud exercitation ullamco laboris nisi ut aliquip ex ea commodo consequat.</p>
      <p>Sincerely,</p>
    </div>
    <div class="signature" role="img" aria-label="Handwritten signature"></div>
  </section>

  <!-- Invoice / quotation -->
  <section class="sheet invoice">
    <div class="sender" style="left:49px;top:43px">Brightpath<br>PO Box 71<br>Kelsdale 3152</div>
    <div class="wordmark"><span class="dot"></span>BRIGHTPATH</div>
    <div class="field" style="left:49px;top:97px">Supplier <i style="width:58px"></i></div>
    <div class="field" style="left:212px;top:99px">Supplier <i style="width:66px"></i></div>
    <div class="item-table">
      <div class="head"><span>Item</span><span>Amount</span></div>
      <div class="total">Total</div>
    </div>
    <div class="field" style="left:51px;top:434px;font-size:8.5px">Supplier <i style="width:82px;height:9px"></i></div>
  </section>

  <!-- A4 envelope -->
  <svg class="a4-flap" width="356" height="54" viewBox="0 0 356 54" aria-hidden="true">
    <defs><linearGradient id="flapGrad" x1="0" y1="0" x2="1" y2="0"><stop offset="0" stop-color="#a8cc32"/><stop offset="1" stop-color="#d3e02a"/></linearGradient></defs>
    <polygon points="28,0 306,0 356,54 0,54" fill="url(#flapGrad)"/>
  </svg>
  <section class="sheet a4-envelope">
    <div class="pattern-area" role="img" aria-label="Decorative pattern of coloured dots and rounded bars in lime, purple, blue, orange and red"></div>
  </section>

  <!-- DL envelope, back -->
  <section class="sheet dl-back">
    <div class="ghost-name">Brightpath</div>
    <svg width="356" height="165" viewBox="0 0 356 165" aria-hidden="true">
      <polygon points="0,4 356,4 316,43 40,43" fill="#fff" stroke="#e2e2e2"/>
    </svg>
  </section>

  <!-- DL envelope, front -->
  <section class="sheet dl-front">
    <div class="wordmark"><span class="dot"></span>BRIGHTPATH</div>
  </section>

  <!-- Business card, front -->
  <section class="sheet card-front">
    <div class="wordmark"><span class="dot"></span>BRIGHTPATH</div>
  </section>

  <!-- Business card, back -->
  <section class="sheet card-back">
    <span class="mark"></span>
    <div class="details">
      <div class="name">Marcus Ferrow</div>
      M. 0472 915 408<br>
      E. mferrow@<br>brightpathcare.example<br>
      A. PO Box 71 Kelsdale
    </div>
  </section>

  <!-- Email signature -->
  <section class="sheet email">
    <div class="toolbar">
      <b></b><span>Send</span><b></b><b></b><b></b><b></b><b></b><b></b><b></b><b></b><b></b><span>Options...</span><span class="sel"></span>
    </div>
    <div class="headers">
      <div class="hrow" style="top:4px"><span>To...</span><span class="box" style="width:306px;padding-left:2px;line-height:6px">dan</span></div>
      <div class="hrow" style="top:17px"><span>Cc...</span><span class="box" style="width:306px"></span></div>
      <div class="hrow" style="top:33px"><span>Subject:</span><span class="box" style="width:312px;padding-left:2px;line-height:6px">Next Week</span></div>
      <div class="suggest">dana.pell@northfield.example<br><span class="hi">Dana Pell [dana.pell@northfield.example]</span></div>
    </div>
    <div class="formatbar">
      <span class="sel"></span><span class="sel" style="width:14px"></span><b></b><b></b><b></b><b></b><b></b><b></b><b></b><b></b><b></b><b></b><b></b>
    </div>
    <div class="mail-body">
      <p>Hi Dana,</p>
      <p>Back to school already! Do you have time to go through the ICT plan today?</p>
      <p>Thanks,</p>
      <div class="sign">Lena</div>
      <div class="addr">PO Box 71<br>Kelsdale 3152</div>
      <div class="wordmark"><span class="dot"></span>BRIGHTPATH</div>
    </div>
  </section>

</body>
</html>
```